Nine Phase Ledger Roadmap Talk

I would like a flyer to hand out to participants at the speeches that we give. We are a CPA firm that specializes in entrepreneurs and realtors. We would like a flyer that looks crisp and clean, that integrates our logo and our company colors (shades of blue & gold). We would like the wording to be as laid out in the attached documents, but design is up to you. We would like a picture to go along with each point and are open to ideas. The flyer should be one page, preferably just the front.

Colors
3176b5
fee18a

Requirements
Must have
• Our logo and the wording supplied.
• A picture to go along with each topic.
Nice to have
• Images that pop, clean look, professional.
Should not have
• Look messy.

```html
<!DOCTYPE html>
<html lang="en">
<head>
<meta charset="utf-8">
<title>Nine Phase Ledger Roadmap Talk Agenda</title>
<link href="https://fonts.googleapis.com/css2?family=Montserrat:wght@800;900&family=Arimo:wght@400;700&family=Libre+Baskerville:ital@1&display=swap" rel="stylesheet">
<style>
  :root {
    --blue: #2460a6;
    --blue-deep: #1d5597;
    --blue-photo: #3f73b3;
    --gold: #f4d06f;
    --gold-bright: #fee18a;
    --paper: #eceef1;
    --ink: #333a44;
    --num-grey: #7c7f86;
    --white: #ffffff;
  }
  * { margin: 0; padding: 0; box-sizing: border-box; }
  html, body { width: 923px; height: 1200px; overflow: hidden; }
  body { background: var(--paper); font-family: "Arimo", Arial, sans-serif; }
  .flyer { position: relative; width: 923px; height: 1200px; background: var(--paper); }
  .top-rule { position: absolute; top: 0; left: 0; width: 100%; height: 6px; background: var(--gold); }
  .header {
    position: absolute; top: 6px; left: 0; width: 100%; height: 296px;
    background: linear-gradient(120deg, #3a6fae 0%, #4b80be 40%, #2f64a6 100%);
  }
  .brand { position: absolute; top: 38px; right: 62px; text-align: right; }
  .brand-name {
    font-family: "Montserrat", sans-serif; font-weight: 900; color: var(--white);
    font-size: 40px; letter-spacing: -1px; line-height: 1;
  }
  .brand-tag {
    font-family: "Libre Baskerville", serif; font-style: italic; color: var(--white);
    font-size: 11px; margin-top: 12px;
  }
  .title {
    position: absolute; left: 70px; top: 176px;
    font-family: "Montserrat", sans-serif; font-weight: 900;
    font-size: 45px; line-height: 1.04; letter-spacing: -0.5px; text-transform: uppercase;
  }
  .title .line-white { color: var(--white); display: block; }
  .title .line-gold { color: var(--gold-bright); display: block; }
  .step {
    position: absolute; width: 274px; padding: 10px 22px 0 26px;
    font-size: 17px; line-height: 20.6px;
  }
  .step.blue { background: var(--blue-deep); color: var(--white); }
  .step.gold { background: var(--gold); color: var(--ink); }
  .step-num {
    font-family: "Montserrat", sans-serif; font-weight: 900; font-size: 28px;
    line-height: 1; margin-bottom: 16px;
  }
  .step.blue .step-num { color: #f3e2b0; }
  .step.gold .step-num { color: var(--num-grey); }
  .col-1 { left: 45px; } .col-2 { left: 329px; } .col-3 { left: 612px; }
  .row-1 { top: 323px; height: 292px; }
  .row-2 { top: 623px; height: 274px; }
  .row-3 { top: 906px; height: 274px; }
  .slogan {
    position: absolute; left: 351px; top: 912px; width: 540px;
    font-family: "Montserrat", sans-serif; font-weight: 900; color: var(--blue-deep);
    font-size: 29.5px; line-height: 36px; text-transform: uppercase; letter-spacing: 0.2px;
  }
  .contact {
    position: absolute; left: 351px; top: 1049px; color: var(--ink);
    font-size: 16px; line-height: 20px;
  }
  .contact p + p { margin-top: 0; }
  .contact .gap { margin-top: 20px; }
  .contact .web { font-weight: 700; }
  .bottom-rule { position: absolute; bottom: 0; left: 0; width: 100%; height: 5px; background: var(--blue); }
</style>
</head>
<body>
<main class="flyer">
  <div class="top-rule"></div>
  <header class="header" role="img" aria-label="Blue-toned photo of a calculator and financial paperwork on a desk">
    <div class="brand">
      <div class="brand-name">Steady Figures</div>
      <div class="brand-tag">A Professional Accounting Corporation</div>
    </div>
    <h1 class="title">
      <span class="line-white">Nine Phase Ledger</span>
      <span class="line-gold">Roadmap Talk Agenda:</span>
    </h1>
  </header>

  <section class="step blue col-1 row-1">
    <div class="step-num">1</div>
    <p>We will first show you how to eliminate much of your self-employment tax on your return by converting your business into an S Corporation. A business owner making over $120,000 per year can save about $12,000 per year by doing this.</p>
  </section>
  <section class="step gold col-2 row-1">
    <div class="step-num">2</div>
    <p>We will show you how to get tax free income from your corporation by renting you home to the corporation for the board meetings. Many of our clients are getting up to $21,000 in tax free income which could put $8,400 cash into your pocket.</p>
  </section>
  <section class="step blue col-3 row-1">
    <div class="step-num">3</div>
    <p>We will show you the easiest way to track your expenses so that the only thing you will have to do to have rock solid books is to take a picture of the receipt and throw it away. It doesn’t get any better than that.</p>
  </section>

  <section class="step gold col-1 row-2">
    <div class="step-num">4</div>
    <p>Next, we show you the importance of tax planning and why it is critical to meet with your CPA before the end of the year and not just when you do your tax preparation.</p>
  </section>
  <section class="step blue col-2 row-2">
    <div class="step-num">5</div>
    <p>We will show you how to hire your children and get $7,500 per child tax free. This will save you $3,000 per child in income tax reduction.</p>
  </section>
  <section class="step gold col-3 row-2">
    <div class="step-num">6</div>
    <p>We will discuss how to make your child’s college education tax deductible. With college cost spiraling out of control this is a biggie.&nbsp;&nbsp; Most of our clients have a savings of about $12,000 per year of college.</p>
  </section>

  <section class="step blue col-1 row-3">
    <div class="step-num">7</div>
    <p>Our grand finale is to show you how to use, not one, but two corporations to get a several hundred thousand dollar tax deferral, get an interest free loan from the government and use that money to grow your business and your wealth.</p>
  </section>

  <p class="slogan">If they drive by with a machine gun you don’t have to stand up.</p>

  <address class="contact" style="font-style: normal;">
    <p>Steady Figures, A Professional Accounting Corporation</p>
    <p>2710 N. Oak Ave, Ste. B, Lindale, CA 95000</p>
    <p>Phone: 555-014-2230 &nbsp;•&nbsp; Fax: 555-014-2231</p>
    <p class="gap">dana@steadyfigurescpas.com</p>
    <p>owen@steadyfigurescpas.com</p>
    <p class="web">www.steadyfigurescpa.com</p>
  </address>

  <div class="bottom-rule"></div>
</main>
</body>
</html>
```